Social Media Graphics - Oakline Push REVISED

Create 6-7 individual social media graphics (square size) to encourage folks to join our online course called:

The Harvest Ledger Circle
How to Launch a Multi-Million Business From Scratch
Sign Up Today!

IMPORTANT: Make the largest and most prominent text on the graphic be: How to Launch a Multi-Million Business From Scratch

For the color scheme of the graphics, let's try a blue color palette; make sure the graphics appeal to both men and women

Make sure each graphic contains 1 of the 3 pics attached (crop pic as needed); and make sure one of the graphics is all TEXT only.

Target Market(s)

men and women looking to start a business

Industry/Entity Type

Entrepreneurship

Colors
0054AA
0677BA
7BADD7
CADEEF
E8F1F8

Requirements
Must have
• All the text and use the 3 pics provided; one graphic can be all text; Simple, modern design that's easy to read

```html
<!DOCTYPE html>
<html lang="en">
<head>
<meta charset="utf-8">
<title>The Harvest Ledger Circle – Social Set</title>
<link href="https://fonts.googleapis.com/css2?family=Outfit:wght@400;500;600;700;800&family=Inter+Tight:wght@700;800;900&display=swap" rel="stylesheet">
<style>
  :root{
    --board:#c9c9c9;
    --navy:#0a12a8;
    --navy-deep:#050b7a;
    --royal:#2f4ff0;
    --bright:#2e63f7;
    --cyan:#17e8ff;
    --sky:#4fd2ff;
    --violet:#7a2ee0;
    --ink:#101035;
    --white:#ffffff;
    --pale:#e8f1f8;
    --photo-a:#3a3f63;
    --photo-b:#1f2340;
  }
  *{box-sizing:border-box;margin:0;padding:0}
  html,body{width:1200px;height:816px;overflow:hidden;background:var(--board)}
  body{position:relative;font-family:"Outfit",sans-serif;color:var(--white)}
  .tile{position:absolute;width:377px;height:377px;overflow:hidden}
  .tile--1{left:25px;top:26px;background:linear-gradient(160deg,var(--navy) 0%,var(--navy-deep) 100%)}
  .tile--2{left:412px;top:26px;background:linear-gradient(135deg,#ffffff 0%,#cfeffd 55%,#7fd9fb 100%)}
  .tile--3{left:798px;top:26px;background:linear-gradient(160deg,#1426d6 0%,var(--navy-deep) 100%)}
  .tile--4{left:25px;top:413px;background:linear-gradient(150deg,#3b6cff 0%,var(--bright) 60%,#2447e0 100%)}
  .tile--5{left:412px;top:413px;background:linear-gradient(160deg,#1c33e6 0%,var(--navy) 100%)}
  .tile--6{left:798px;top:413px;background:linear-gradient(160deg,#1426d6 0%,var(--navy-deep) 100%)}

  .swirl{position:absolute;border-radius:50%;filter:blur(2px)}
  .swirl--cyan{background:radial-gradient(circle at 40% 40%,var(--cyan) 0%,#1aa8ff 45%,rgba(60,60,255,0) 72%)}
  .swirl--violet{background:radial-gradient(circle at 50% 50%,#8c3cff 0%,rgba(110,50,230,0) 70%)}

  .photo{position:absolute;background:linear-gradient(180deg,var(--photo-a),var(--photo-b))}
  .photo--warm{background:linear-gradient(90deg,#c23a5a 0%,#3a2a2e 55%,#1d1d26 100%)}
  .photo--blue{background:linear-gradient(90deg,#2a2a33 0%,#2b3b66 60%,#2d4f8a 100%)}
  .photo--stage{background:linear-gradient(180deg,#c9c2ba 0%,#8d857e 40%,#3c3a48 100%)}

  .spark{position:absolute}
  .watermark{position:absolute;font-family:"Inter Tight",sans-serif;font-weight:900;line-height:1;letter-spacing:-2px;white-space:nowrap}
  .tag{position:absolute;font-size:12px;padding:3px 10px;border-radius:14px;white-space:nowrap}
  .tag--cyan{background:var(--sky);color:var(--ink)}
  .tag--violet{background:var(--violet);color:var(--white);border:1px solid #c9b2ff}
  .display{font-family:"Inter Tight",sans-serif;font-weight:800;letter-spacing:-1px;line-height:1}

  .cta{position:absolute;font-family:"Inter Tight",sans-serif;font-weight:800;line-height:.95;letter-spacing:-1px;text-align:center;border:1.5px solid #ffffff;transform:rotate(-5deg)}
  .cta::before,.cta::after{content:"";position:absolute;width:5px;height:5px;background:#fff}
  .cta::before{left:-3px;top:-3px}
  .cta::after{right:-3px;bottom:-3px}
  .cta--royal{background:var(--royal)}
  .cta--ink{background:var(--ink)}

  /* tile 1 */
  .lead-card{position:absolute;left:55px;top:109px;width:267px;height:143px;background:var(--white);border-radius:6px;color:var(--ink);text-align:center}
  .lead-card .line{font-size:21px;font-weight:500}
  .lead-card .pill{display:inline-block;margin:6px 0;background:var(--royal);color:var(--white);font-family:"Inter Tight",sans-serif;font-weight:800;letter-spacing:-.6px;font-size:19px;padding:6px 14px;border-radius:20px}

  /* tile 2 */
  .title-box{position:absolute;left:53px;top:58px;width:267px;height:122px;background:var(--royal);border-radius:6px;text-align:center;padding-top:22px}
  .title-box .kicker{font-size:22px;font-weight:500}
  .title-box .name{font-size:34px;margin-top:4px}
</style>
</head>
<body>

<svg width="0" height="0" style="position:absolute">
  <defs>
    <g id="spark"><path d="M10 1V19M2.2 5.5L17.8 14.5M17.8 5.5L2.2 14.5" stroke="currentColor" stroke-width="3.6" stroke-linecap="round"/></g>
  </defs>
</svg>

<!-- Tile 1: text only -->
<section class="tile tile--1">
  <div class="watermark" style="left:10px;top:48px;font-size:64px;color:#1b2ad0">CIRCLE CIRCLE</div>
  <div class="watermark" style="left:10px;top:342px;font-size:64px;color:#1b2ad0">CIRCLE CIRCLE</div>
  <div class="swirl swirl--cyan" style="left:150px;top:120px;width:260px;height:260px"></div>
  <div class="swirl swirl--violet" style="left:240px;top:70px;width:150px;height:150px"></div>
  <div class="swirl swirl--cyan" style="left:40px;top:250px;width:190px;height:190px"></div>
  <svg class="spark" style="left:90px;top:40px;color:var(--sky)" width="30" height="30" viewBox="0 0 20 20"><use href="#spark"/></svg>
  <svg class="spark" style="left:292px;top:76px;color:var(--sky)" width="14" height="14" viewBox="0 0 20 20"><use href="#spark"/></svg>
  <svg class="spark" style="left:35px;top:258px;color:#fff" width="14" height="14" viewBox="0 0 20 20"><use href="#spark"/></svg>
  <svg class="spark" style="left:108px;top:333px;color:#fff" width="18" height="18" viewBox="0 0 20 20"><use href="#spark"/></svg>
  <div class="lead-card">
    <p class="line" style="margin-top:28px">How to Launch a</p>
    <span class="pill">Multi-Million Business</span>
    <p class="line">from Scratch</p>
  </div>
  <span class="tag tag--cyan" style="left:210px;top:100px;transform:rotate(14deg)">Sign Up Today!</span>
  <span class="tag tag--violet" style="left:26px;top:218px;transform:rotate(-10deg)">online course</span>
</section>

<!-- Tile 2 -->
<section class="tile tile--2">
  <div class="swirl swirl--cyan" style="left:60px;top:-30px;width:200px;height:140px"></div>
  <div class="swirl swirl--violet" style="left:-30px;top:110px;width:110px;height:90px"></div>
  <div class="watermark" style="left:-4px;top:200px;font-size:58px;color:#59a8f6;opacity:.8">CIRCLE<br>CIRCLE<br>CIRCLE</div>
  <div class="photo photo--blue" role="img" aria-label="Photo of the two course hosts smiling, arms crossed" style="left:31px;top:188px;width:325px;height:189px;border-radius:4px 4px 0 0"></div>
  <div class="title-box">
    <p class="kicker">The Harvest Ledger</p>
    <p class="display name">CIRCLE</p>
  </div>
  <svg class="spark" style="left:82px;top:86px;color:#fff" width="13" height="13" viewBox="0 0 20 20"><use href="#spark"/></svg>
  <svg class="spark" style="left:287px;top:150px;color:#fff" width="13" height="13" viewBox="0 0 20 20"><use href="#spark"/></svg>
  <svg class="spark" style="left:330px;top:28px;color:#2a6cf5" width="32" height="32" viewBox="0 0 20 20"><use href="#spark"/></svg>
  <svg class="spark" style="left:32px;top:190px;color:#2a9cf5" width="22" height="22" viewBox="0 0 20 20"><use href="#spark"/></svg>
  <span class="tag tag--violet" style="left:70px;top:44px;transform:rotate(-6deg)">Sign Up Today!</span>
</section>

<!-- Tile 3 -->
<section class="tile tile--3">
  <div class="swirl swirl--cyan" style="left:-20px;top:-20px;width:140px;height:140px"></div>
  <div class="swirl swirl--cyan" style="left:240px;top:260px;width:160px;height:150px"></div>
  <div class="photo photo--warm" role="img" aria-label="Photo of the two course hosts, arms crossed" style="left:16px;top:118px;width:274px;height:259px;border-radius:4px 4px 0 0"></div>
  <p style="position:absolute;right:24px;top:32px;font-family:'Inter Tight',sans-serif;font-weight:800;letter-spacing:-1px;font-size:24px;color:var(--cyan)">The Harvest Ledger</p>
  <p class="display" style="position:absolute;left:24px;top:66px;width:330px;text-align:center;font-size:60px;letter-spacing:-2px">CIRCLE</p>
  <p style="position:absolute;left:245px;top:118px;width:125px;font-size:13px;font-weight:600;line-height:1.05">How to Launch a Multi-Million Business From Scratch.</p>
  <svg class="spark" style="left:145px;top:26px;color:#fff" width="22" height="22" viewBox="0 0 20 20"><use href="#spark"/></svg>
  <svg class="spark" style="left:318px;top:188px;color:var(--sky)" width="14" height="14" viewBox="0 0 20 20"><use href="#spark"/></svg>
  <div class="cta cta--royal" style="left:230px;top:236px;width:120px;height:74px;font-size:27px;padding-top:8px">Sign Up<br>Today!</div>
</section>

<!-- Tile 4 -->
<section class="tile tile--4">
  <div class="swirl swirl--cyan" style="left:250px;top:-40px;width:160px;height:180px"></div>
  <div class="swirl swirl--cyan" style="left:-30px;top:290px;width:130px;height:120px"></div>
  <div class="photo photo--warm" role="img" aria-label="Photo of the two course hosts smiling" style="left:165px;top:125px;width:212px;height:252px;border-radius:4px 0 0 0"></div>
  <span style="position:absolute;left:14px;top:33px;background:var(--ink);border:1px solid #fff;padding:2px 10px;font-size:25px;font-weight:600;transform:rotate(-2deg)">How to</span>
  <p style="position:absolute;left:26px;top:74px;font-size:29px;font-weight:600">Launch a</p>
  <p class="display" style="position:absolute;left:26px;top:111px;font-size:40px;color:var(--cyan)">Multi-Million<br>Business</p>
  <p style="position:absolute;left:26px;top:194px;font-size:30px;font-weight:600;line-height:1">From<br>Scratch!</p>
  <svg class="spark" style="left:228px;top:48px;color:#fff" width="22" height="22" viewBox="0 0 20 20"><use href="#spark"/></svg>
  <div class="cta cta--ink" style="left:76px;top:265px;width:120px;height:74px;font-size:27px;padding-top:8px">Sign Up<br>Today!</div>
</section>

<!-- Tile 5 -->
<section class="tile tile--5">
  <div class="swirl swirl--cyan" style="left:150px;top:-30px;width:200px;height:150px"></div>
  <div class="swirl swirl--violet" style="left:270px;top:20px;width:120px;height:100px"></div>
  <p class="display" style="position:absolute;left:27px;top:33px;font-size:27px;line-height:1">The Harvest<br>Ledger</p>
  <p class="display" style="position:absolute;left:26px;top:348px;font-size:40px;transform:rotate(-90deg);transform-origin:0 0;letter-spacing:-1.5px">CIRCLE</p>
  <div style="position:absolute;left:69px;top:116px;width:49px;height:230px;background:var(--royal);border:1.5px solid #fff"></div>
  <p style="position:absolute;left:79px;top:340px;width:220px;font-size:12px;font-weight:500;line-height:1.15;transform:rotate(-90deg);transform-origin:0 0">How to Launch a Multi-Million<br>Business From Scratch.</p>
  <svg class="spark" style="left:108px;top:130px;color:var(--sky)" width="20" height="20" viewBox="0 0 20 20"><use href="#spark"/></svg>
  <svg class="spark" style="left:257px;top:22px;color:#fff" width="22" height="22" viewBox="0 0 20 20"><use href="#spark"/></svg>
  <div class="photo photo--blue" role="img" aria-label="Photo of the two course hosts, arms crossed" style="left:158px;top:84px;width:190px;height:241px;border-radius:10px"></div>
  <span class="tag tag--cyan" style="left:206px;top:306px;font-size:14px;padding:4px 12px;transform:rotate(-5deg)">Sign Up Today!</span>
</section>

<!-- Tile 6 -->
<section class="tile tile--6">
  <div class="photo photo--stage" role="img" aria-label="Photo of the two hosts speaking on stage with a microphone" style="left:188px;top:0;width:189px;height:377px"></div>
  <div class="swirl swirl--cyan" style="left:-10px;top:-40px;width:150px;height:110px"></div>
  <div class="swirl swirl--cyan" style="left:100px;top:300px;width:260px;height:120px"></div>
  <span style="position:absolute;left:19px;top:106px;background:var(--cyan);color:var(--ink);padding:1px 8px;font-size:21px;font-weight:600;transform:rotate(-3deg)">How to</span>
  <p style="position:absolute;left:23px;top:133px;font-size:21px;font-weight:600;line-height:1.12">Launch a<br><span style="color:var(--sky)">Multi-Million<br>Business</span><br>From Scratch.</p>
  <svg class="spark" style="left:136px;top:81px;color:#fff" width="22" height="22" viewBox="0 0 20 20"><use href="#spark"/></svg>
  <svg class="spark" style="left:25px;top:298px;color:#fff" width="13" height="13" viewBox="0 0 20 20"><use href="#spark"/></svg>
  <svg class="spark" style="left:83px;top:265px;color:var(--sky)" width="30" height="30" viewBox="0 0 20 20"><use href="#spark"/></svg>
  <div class="cta cta--royal" style="left:99px;top:259px;width:120px;height:74px;font-size:27px;padding-top:8px">Sign Up<br>Today!</div>
</section>

</body>
</html>
```